Design Cloud for Core Values & Attributes

See Image Example Below "Word Cloud" this is what we would like this to look like.
The second image is all of the Core Value and Attributes I will list below.
CORE VALUES need to be the bigger words (based off the image I sent) Capitalized, BOLD, Navy
Independence, Capitalism, Trust, Fun, Safety, Growth
ATTRIBUTES need to be the smaller words, lower case, non-bold, lighter blue mixed in (based off the image I sent):
Humility, Consistency, Open Mindedness, Curiosity, Selflessness, Caring, Conscientiousness, Honorable, Cunning, Competitive, Compartmentalization, Innovative, Perseverance, Authenticity, Decisiveness, Self-efficacy, Accountability, Generosity, Humor, Optimism, Resilience, Inclusive, Insouciance to what others think, Courage, Decisive, Curious, Integrity

```html
<!DOCTYPE html>
<html lang="en">
<head>
<meta charset="utf-8">
<title>Core Value Word Cloud</title>
<link rel="stylesheet" href="https://fonts.googleapis.com/css2?family=Montserrat:wght@400;700;800&display=swap">
<style>
  :root {
    --paper: #ffffff;
    --core-navy: #0054a6;
    --attribute-blue: #1b76bc;
  }
  html, body {
    margin: 0;
    padding: 0;
    width: 1200px;
    height: 1200px;
    overflow: hidden;
    background: var(--paper);
  }
  .word-cloud {
    display: block;
    width: 1200px;
    height: 1200px;
  }
  .headline {
    font-family: "Montserrat", sans-serif;
    font-weight: 800;
    font-size: 167px;
    fill: var(--core-navy);
  }
  .core-value {
    font-family: "Montserrat", sans-serif;
    font-weight: 700;
    font-size: 68px;
    fill: var(--core-navy);
  }
  .attribute {
    font-family: "Montserrat", sans-serif;
    font-weight: 400;
    font-size: 45px;
    fill: var(--attribute-blue);
  }
</style>
</head>
<body>
<svg class="word-cloud" viewBox="290 305 1320 1320" xmlns="http://www.w3.org/2000/svg" role="img" aria-label="Core value word cloud">
  <g lengthAdjust="spacingAndGlyphs">
    <!-- Headline -->
    <text class="headline" x="463" y="862" textLength="481" lengthAdjust="spacingAndGlyphs">CORE</text>
    <text class="headline" x="655" y="1008" textLength="585" lengthAdjust="spacingAndGlyphs">VALUE</text>

    <!-- Core values -->
    <text class="core-value" x="683" y="573" textLength="152" lengthAdjust="spacingAndGlyphs">Trust</text>
    <text class="core-value" transform="translate(898 665) rotate(-90)" textLength="105" lengthAdjust="spacingAndGlyphs">Fun</text>
    <text class="core-value" x="965" y="795" textLength="330" lengthAdjust="spacingAndGlyphs">Capitalism</text>
    <text class="core-value" x="965" y="866" textLength="200" lengthAdjust="spacingAndGlyphs">Safety</text>
    <text class="core-value" x="490" y="1078" textLength="443" lengthAdjust="spacingAndGlyphs">Independence</text>
    <text class="core-value" x="1015" y="1288" textLength="235" lengthAdjust="spacingAndGlyphs">Growth</text>

    <!-- Attributes: upper left -->
    <text class="attribute" x="625" y="620" textLength="210" lengthAdjust="spacingAndGlyphs">OPTIMISM</text>
    <text class="attribute" x="522" y="665" textLength="313" lengthAdjust="spacingAndGlyphs">DECISIVENESS</text>
    <text class="attribute" x="340" y="721" textLength="568" lengthAdjust="spacingAndGlyphs">COMPARTMENTALIZATION</text>
    <text class="attribute" transform="translate(953 720) rotate(-90)" textLength="200" lengthAdjust="spacingAndGlyphs">CUNNING</text>

    <!-- Attributes: upper right -->
    <text class="attribute" x="977" y="551" textLength="228" lengthAdjust="spacingAndGlyphs">INTEGRITY</text>
    <text class="attribute" x="975" y="594" textLength="278" lengthAdjust="spacingAndGlyphs">GENEROSITY</text>
    <text class="attribute" x="979" y="641" textLength="291" lengthAdjust="spacingAndGlyphs">COMPETITIVE</text>
    <text class="attribute" x="977" y="687" textLength="325" lengthAdjust="spacingAndGlyphs">SELFLESSNESS</text>
    <text class="attribute" x="975" y="734" textLength="350" lengthAdjust="spacingAndGlyphs">PERSEVERANCE</text>
    <text class="attribute" x="1178" y="863" textLength="380" lengthAdjust="spacingAndGlyphs">ACCOUNTABILITY</text>

    <!-- Attributes: middle left -->
    <text class="attribute" x="441" y="912" textLength="196" lengthAdjust="spacingAndGlyphs">HUMILITY</text>
    <text class="attribute" x="441" y="965" textLength="197" lengthAdjust="spacingAndGlyphs">DECISIVE</text>
    <text class="attribute" x="392" y="1016" textLength="278" lengthAdjust="spacingAndGlyphs">HONORABLE</text>

    <!-- Attributes: middle right -->
    <text class="attribute" x="1257" y="913" textLength="215" lengthAdjust="spacingAndGlyphs">COURAGE</text>
    <text class="attribute" x="1257" y="965" textLength="161" lengthAdjust="spacingAndGlyphs">HUMOR</text>
    <text class="attribute" x="1257" y="1015" textLength="168" lengthAdjust="spacingAndGlyphs">CARING</text>
    <text class="attribute" transform="translate(1468 1120) rotate(-90)" textLength="192" lengthAdjust="spacingAndGlyphs">CURIOUS</text>
    <text class="attribute" x="954" y="1075" textLength="471" lengthAdjust="spacingAndGlyphs">CONSCIENTIOUSNESS</text>
    <text class="attribute" x="563" y="1128" textLength="857" lengthAdjust="spacingAndGlyphs">INSOUCIANCE TO WHAT OTHERS THINK</text>

    <!-- Attributes: lower -->
    <text class="attribute" x="704" y="1180" textLength="231" lengthAdjust="spacingAndGlyphs">CURIOSITY</text>
    <text class="attribute" x="710" y="1227" textLength="225" lengthAdjust="spacingAndGlyphs">INCLUSIVE</text>
    <text class="attribute" x="628" y="1275" textLength="307" lengthAdjust="spacingAndGlyphs">CONSISTENCY</text>
    <text class="attribute" x="617" y="1322" textLength="318" lengthAdjust="spacingAndGlyphs">AUTHENTICITY</text>
    <text class="attribute" x="597" y="1369" textLength="338" lengthAdjust="spacingAndGlyphs">SELF-EFFICACY</text>
    <text class="attribute" transform="translate(991 1413) rotate(-90)" textLength="260" lengthAdjust="spacingAndGlyphs">INNOVATIVE</text>
    <text class="attribute" x="1014" y="1177" textLength="250" lengthAdjust="spacingAndGlyphs">RESILIENCE</text>
    <text class="attribute" x="1015" y="1227" textLength="420" lengthAdjust="spacingAndGlyphs">OPEN MINDEDNESS</text>
  </g>
</svg>
</body>
</html>
```